wealth management firm, professional group, new model

we have a logo that works but we need a card, white background using our colors...clean look

our tag line if can be used in

The Path From Saver to Investor

```html
<!DOCTYPE html>
<html lang="en">
<head>
<meta charset="utf-8">
<title>ARVEN Wealth Partners – Business Card</title>
<link rel="stylesheet" href="https://fonts.googleapis.com/css2?family=Montserrat:wght@400;500;700&display=swap">
<style>
  :root {
    --navy: #1b2d52;
    --navy-deep: #162646;
    --navy-soft: #24396a;
    --white: #ffffff;
    --ink: #1a1a1a;
    --stage: #3a3a3a;
  }
  * { box-sizing: border-box; margin: 0; padding: 0; }
  html, body { width: 1200px; height: 694px; overflow: hidden; }
  body {
    background: var(--stage);
    font-family: "Montserrat", Arial, sans-serif;
    position: relative;
  }
  .card {
    position: absolute;
    top: 192px;
    width: 540px;
    height: 310px;
    border-radius: 22px;
    overflow: hidden;
  }
  /* Back side */
  .card-back { left: 40px; background: var(--navy); }
  .back-pattern {
    position: absolute; inset: 0;
    background: linear-gradient(135deg, var(--navy-soft) 0%, var(--navy) 55%, var(--navy-deep) 100%);
  }
  .back-content {
    position: absolute; inset: 0;
    display: flex; flex-direction: column; align-items: center; justify-content: center;
    gap: 16px; color: var(--white);
  }
  .back-brand {
    display: flex; align-items: center; gap: 10px;
    font-weight: 500; font-size: 22px; letter-spacing: 10px; margin-right: -10px;
  }
  .brand-dot { width: 9px; height: 9px; border-radius: 50%; background: currentColor; }
  .tagline { font-size: 17px; font-weight: 400; letter-spacing: 0.5px; }

  /* Front side */
  .card-front { left: 620px; background: var(--white); color: var(--navy); }
  .front-brand {
    position: absolute; top: 40px; right: 40px; text-align: center;
  }
  .front-brand .brand-name {
    font-size: 34px; font-weight: 500; letter-spacing: 18px; margin-right: -18px;
    display: flex; align-items: center; gap: 12px;
  }
  .front-brand .brand-sub {
    font-size: 10.5px; font-weight: 500; letter-spacing: 3.5px; margin-top: 6px;
  }
  .divider-long {
    position: absolute; top: 128px; left: 210px; right: 22px;
    border-top: 1px solid var(--ink);
  }
  .person { position: absolute; left: 36px; top: 150px; }
  .person-name { font-size: 23px; font-weight: 700; letter-spacing: 0.5px; }
  .person-role { font-size: 13px; font-weight: 400; letter-spacing: 1px; margin-top: 2px; }
  .divider-short { width: 196px; border-top: 1px solid var(--ink); margin: 10px 0 10px; }
  .contacts { list-style: none; color: var(--ink); font-size: 12px; }
  .contacts li { display: flex; align-items: center; gap: 10px; height: 20px; }
  .contacts svg { width: 14px; height: 14px; fill: var(--navy); flex: none; }
  .address {
    position: absolute; right: 36px; top: 196px;
    text-align: right; font-size: 12px; line-height: 1.5; color: var(--ink);
    font-style: normal;
  }
  .bottom-band { position: absolute; left: 0; bottom: 0; width: 540px; height: 40px; }
</style>
</head>
<body>

<section class="card card-back" aria-label="Card back">
  <div class="back-pattern" role="img" aria-label="Subtle tonal pattern of repeating arcs on navy"></div>
  <div class="back-content">
    <div class="back-brand"><span class="brand-dot"></span>ARVEN</div>
    <p class="tagline">The Path From Saver to Investor</p>
  </div>
</section>

<section class="card card-front" aria-label="Card front">
  <div class="front-brand">
    <div class="brand-name"><span class="brand-dot"></span>ARVEN</div>
    <div class="brand-sub">WEALTH PARTNERS</div>
  </div>
  <div class="divider-long"></div>

  <div class="person">
    <h1 class="person-name">DANIEL HART</h1>
    <p class="person-role">MANAGING DIRECTOR</p>
    <div class="divider-short"></div>
    <ul class="contacts">
      <li>
        <svg viewBox="0 0 24 24" aria-hidden="true"><path d="M6.6 10.8a15.1 15.1 0 0 0 6.6 6.6l2.2-2.2a1 1 0 0 1 1-.25 11.4 11.4 0 0 0 3.6.57 1 1 0 0 1 1 1V20a1 1 0 0 1-1 1A17 17 0 0 1 3 4a1 1 0 0 1 1-1h3.5a1 1 0 0 1 1 1c0 1.25.2 2.45.57 3.6a1 1 0 0 1-.25 1z"/></svg>
        044-555 218 640
      </li>
      <li>
        <svg viewBox="0 0 24 24" aria-hidden="true"><rect x="2" y="5" width="20" height="14" rx="1"/><path d="M3 6l9 7 9-7" stroke="#fff" stroke-width="1.6" fill="none"/></svg>
        info@arvenwealth.com
      </li>
      <li>
        <svg viewBox="0 0 24 24" aria-hidden="true"><circle cx="12" cy="12" r="10"/><path d="M2 12h20M12 2c3 3 3 17 0 20M12 2c-3 3-3 17 0 20" stroke="#fff" stroke-width="1.4" fill="none"/></svg>
        www.arvenwealth.com
      </li>
    </ul>
  </div>

  <address class="address">
    88 Harbour Lane, Suite 4<br>40211, Marlow Bay
  </address>

  <svg class="bottom-band" viewBox="0 0 540 40" aria-hidden="true">
    <polygon points="0,34 300,34 312,20 540,20 540,40 0,40" fill="var(--navy)"/>
    <polygon points="300,34 312,20 318,20 306,34" fill="var(--white)"/>
  </svg>
</section>

</body>
</html>
```